Dietitian needs awesome business card

I need a contemporary design that's eye catching but professional.
My card is to given to doctors, specialists and patients alike.
I manage patients with chronic diseases
I have uploaded my logo and current business card, I would also like the other Certified Clinical Nutritionist logo incorporated into the design

Target Market(s)

Doctors, specialists and patients

Industry/Entity Type

Healthcare

Contact Information for Business Card

www.brightfieldnutrition.com.au
Ph: 0427 561 903
Fax: 6457 2183
email: marcus.k.diet@fernmail.com
Space on the back of the card with: Appointment date, Appointment time and appointment location

Font styles to use
Serif

Colors
fbee3e
876aae
ffc214

Requirements
Must have
• My Logo
• Certified Clinical Nutritionist Logo
• My 4 locations - Pinebrook Medical Centre, North Corrin Health, Hollis Medical, Ashcombe Doctors Surgery
Nice to have
• I like the colours in my current business card

```html
<!DOCTYPE html>
<html lang="en">
<head>
<meta charset="utf-8">
<title>Brightfield Nutrition &amp; Dietetics – Business Card</title>
<link href="https://fonts.googleapis.com/css2?family=Arimo:wght@400;700&display=swap" rel="stylesheet">
<style>
  :root{
    --bg:#2f3033;
    --card:#ffffff;
    --navy:#1f2f96;
    --blue:#1a7fd0;
    --green:#7cc242;
    --lime:#b7d84a;
    --orange:#f47c20;
    --ink:#2c3a8a;
    --rule:#9aa0b0;
    --grey:#55596a;
  }
  *{box-sizing:border-box;margin:0;padding:0}
  html,body{width:1200px;height:950px;overflow:hidden}
  body{background:var(--bg);font-family:"Arimo",Arial,sans-serif;position:relative}
  .card{position:absolute;left:250px;width:700px;height:428px;background:var(--card);overflow:hidden;box-shadow:0 6px 18px rgba(0,0,0,.35)}
  .card--back{top:32px}
  .card--front{top:490px}

  /* brand lockup */
  .brand{position:absolute;display:flex;align-items:center;gap:14px}
  .brand__dot{width:64px;height:64px;border-radius:50%;background:var(--blue);flex:none}
  .brand__name{font-weight:400;color:var(--navy);line-height:1.05}
  .brand__name span{display:block}
  .brand__name .top{font-size:44px}
  .brand__name .sub{font-size:22px}

  /* back side */
  .card--back .brand{left:48px;top:128px}
  .credential{position:absolute;right:48px;top:34px;width:190px;height:70px;background:var(--orange);display:flex;align-items:center;gap:12px;padding:0 14px}
  .credential__text{color:#fff;font-size:12px;line-height:1.25}
  .credential__mark{width:36px;height:36px;background:#fff;flex:none;margin-left:auto}
  .rule{position:absolute;height:1px;background:var(--rule)}
  .field-label{position:absolute;font-size:17px;color:var(--ink);line-height:20px}
  .ampm{position:absolute;font-size:13px;color:var(--ink);line-height:16px}
  .locations{position:absolute;list-style:none;font-size:16px;color:var(--grey)}
  .locations li{display:flex;align-items:center;gap:9px;height:24px}
  .locations li::before{content:"";width:12px;height:12px;border:1.5px solid var(--ink);flex:none}

  /* front side */
  .card--front .brand{left:150px;top:90px}
  .card--front .brand__dot{width:86px;height:86px}
  .card--front .brand__name .top{font-size:56px}
  .card--front .brand__name .sub{font-size:26px}
  .band{position:absolute;inset:0}
  .person{position:absolute;right:40px;top:262px;text-align:right;color:#fff}
  .person__name{font-size:26px;font-weight:700}
  .person__role{font-size:17px;font-weight:700;margin-top:4px}
  .contacts{position:absolute;left:40px;top:316px;list-style:none;color:#fff;font-size:17px}
  .contacts li{display:flex;align-items:center;gap:12px;height:24px}
  .contacts svg{width:16px;height:16px;flex:none}
</style>
</head>
<body>

<section class="card card--back" aria-label="Appointment side">
  <div class="credential">
    <span class="credential__text">Certified<br>Clinical<br>Nutritionist</span>
    <span class="credential__mark"></span>
  </div>

  <div class="brand">
    <span class="brand__dot"></span>
    <span class="brand__name"><span class="top">Brightfield</span><span class="sub">Nutrition &amp; Dietetics</span></span>
  </div>

  <!-- right column: time -->
  <div class="rule" style="left:420px;top:126px;width:232px"></div>
  <div class="ampm" style="left:612px;top:146px">AM/PM</div>
  <div class="rule" style="left:420px;top:164px;width:232px"></div>
  <div class="field-label" style="left:420px;top:180px">Time :</div>
  <div class="rule" style="left:478px;top:198px;width:174px"></div>
  <ul class="locations" style="left:420px;top:214px">
    <li>Ashcombe Doctors Surgery</li>
    <li>Hollis Medical</li>
  </ul>

  <!-- left column: date -->
  <div class="rule" style="left:100px;top:230px;width:290px"></div>
  <div class="rule" style="left:100px;top:270px;width:290px"></div>
  <div class="rule" style="left:100px;top:310px;width:290px"></div>
  <div class="field-label" style="left:48px;top:332px">Date :</div>
  <div class="rule" style="left:106px;top:350px;width:284px"></div>
  <ul class="locations" style="left:48px;top:366px">
    <li>Pinebrook Medical Centre</li>
    <li>North Corrin Health</li>
  </ul>
</section>

<section class="card card--front" aria-label="Contact side">
  <div class="brand">
    <span class="brand__dot"></span>
    <span class="brand__name"><span class="top">Brightfield</span><span class="sub">Nutrition &amp; Dietetics</span></span>
  </div>

  <svg class="band" viewBox="0 0 700 428" preserveAspectRatio="none" aria-hidden="true">
    <defs>
      <linearGradient id="bandFill" x1="0" y1="1" x2="1" y2="0">
        <stop offset="0" stop-color="#1f2a8f"/>
        <stop offset="0.55" stop-color="#1d4fb8"/>
        <stop offset="1" stop-color="#1a8ad6"/>
      </linearGradient>
    </defs>
    <path d="M0 268 C230 258 470 220 700 88 L700 104 C470 238 230 276 0 284 Z" fill="var(--lime)"/>
    <path d="M0 292 C240 284 480 246 700 116 L700 428 L0 428 Z" fill="url(#bandFill)"/>
    <path d="M0 300 C240 292 480 256 700 128" fill="none" stroke="#fff" stroke-width="2"/>
  </svg>

  <div class="person">
    <div class="person__name">Marcus Kellerman</div>
    <div class="person__role">Nutritionist &amp; Chef</div>
  </div>

  <ul class="contacts">
    <li><svg viewBox="0 0 16 16"><path d="M3 2h3l1 3-2 1a8 8 0 0 0 5 5l1-2 3 1v3a1 1 0 0 1-1 1A12 12 0 0 1 2 3a1 1 0 0 1 1-1z" fill="#fff"/></svg>0427 561 903</li>
    <li><svg viewBox="0 0 16 16"><rect x="2" y="6" width="12" height="8" rx="1" fill="#fff"/><rect x="4" y="2" width="8" height="5" fill="#fff"/><rect x="5" y="9" width="6" height="1.5" fill="#1f2f96"/></svg>6457 2183</li>
    <li><svg viewBox="0 0 16 16"><rect x="1" y="3" width="14" height="10" rx="1" fill="#fff"/><path d="M1.5 4 8 9l6.5-5" fill="none" stroke="#1f2f96" stroke-width="1.4"/></svg>marcus.k.diet@fernmail.com</li>
    <li><svg viewBox="0 0 16 16"><circle cx="8" cy="8" r="7" fill="#fff"/><path d="M1 8h14M8 1c-3 3-3 11 0 14M8 1c3 3 3 11 0 14" fill="none" stroke="#1f2f96" stroke-width="1"/></svg>www.brightfieldnutrition.com.au</li>
  </ul>
</section>

</body>
</html>
```